Veldmark Supplies Business Card

Professional business card that stand out to our potential customers. Front and back with clean modern design

Industry/Entity Type

Oil and gas

Contact Information for Business Card

Name, address, website , office phone and cell number

Requirements
Must have
• Editable files for each employee

```html
<!DOCTYPE html>
<html lang="en">
<head>
<meta charset="utf-8">
<title>Veldmark Supplies Business Card</title>
<link href="https://fonts.googleapis.com/css2?family=Montserrat:wght@700;800&family=Open+Sans:wght@400;600&display=swap" rel="stylesheet">
<style>
  :root {
    --stage: #2b2b2d;
    --card: #1b1b1c;
    --card-back: #151516;
    --red: #ff0d0d;
    --blue: #00afd6;
    --white: #ffffff;
    --mark-dark: #0b0b0b;
    --edge: #2c2a3a;
  }
  * { margin: 0; padding: 0; box-sizing: border-box; }
  html, body {
    width: 1200px; height: 694px; overflow: hidden;
    background: var(--stage);
  }
  .canvas {
    position: relative; width: 1200px; height: 694px;
  }
  .card {
    position: absolute; top: 192px;
    width: 540px; height: 310px;
    border-radius: 22px; overflow: hidden;
  }
  /* Back side */
  .card--back {
    left: 30px;
    background: var(--card-back);
    border: 1px solid var(--edge);
    display: flex; align-items: center; justify-content: center;
  }
  .back-brand {
    display: flex; align-items: center; gap: 14px;
    font-family: "Montserrat", sans-serif; font-weight: 800;
    font-size: 30px; letter-spacing: 1px; text-transform: uppercase;
    color: var(--mark-dark);
  }
  .back-brand .brand-square {
    width: 26px; height: 26px; background: var(--mark-dark);
  }
  /* Front side */
  .card--front {
    left: 630px;
    background: var(--card);
  }
  .front-brand {
    position: absolute; left: 40px; top: 130px; width: 230px;
    display: flex; align-items: center; gap: 10px;
    font-family: "Montserrat", sans-serif; font-weight: 800;
    font-size: 19px; letter-spacing: 0.5px; text-transform: uppercase;
    color: var(--red);
  }
  .front-brand .brand-square {
    flex: none; width: 18px; height: 18px; background: var(--blue);
  }
  .divider {
    position: absolute; left: 286px; top: 40px;
    width: 1.5px; height: 200px; background: var(--red);
  }
  .contact {
    position: absolute; left: 306px; top: 40px; width: 220px;
    font-family: "Open Sans", sans-serif; color: var(--white);
  }
  .contact__name {
    font-family: "Montserrat", sans-serif; font-weight: 800;
    font-size: 22px; color: var(--red); line-height: 1.1;
  }
  .contact__role {
    font-size: 13px; color: var(--blue); margin-top: 2px;
  }
  .contact__address {
    font-size: 12px; line-height: 1.45; margin-top: 10px;
  }
  .contact__list { list-style: none; margin-top: 12px; }
  .contact__list li {
    display: flex; align-items: center; gap: 9px;
    font-size: 12px; line-height: 1; margin-bottom: 8px;
  }
  .contact__list svg { width: 14px; height: 14px; flex: none; }
  .stripe {
    position: absolute; left: 0; right: 0; bottom: 0; height: 7px;
    display: flex;
  }
  .stripe__red { flex: 7; background: var(--red); }
  .stripe__blue { flex: 3; background: var(--blue); }
</style>
</head>
<body>
<main class="canvas">
  <section class="card card--back" aria-label="Card back">
    <div class="back-brand"><span class="brand-square"></span>Veldmark Supplies</div>
  </section>

  <section class="card card--front" aria-label="Card front">
    <div class="front-brand"><span class="brand-square"></span>Veldmark Supplies</div>
    <div class="divider"></div>
    <div class="contact">
      <h1 class="contact__name">Marcus Hale</h1>
      <p class="contact__role">Owner</p>
      <p class="contact__address">421, Address line goes here<br>45452, Country name</p>
      <ul class="contact__list">
        <li>
          <svg viewBox="0 0 24 24" fill="var(--blue)"><path d="M6.6 10.8a15.1 15.1 0 0 0 6.6 6.6l2.2-2.2a1 1 0 0 1 1-.25 11.4 11.4 0 0 0 3.6.57 1 1 0 0 1 1 1V20a1 1 0 0 1-1 1A17 17 0 0 1 3 4a1 1 0 0 1 1-1h3.5a1 1 0 0 1 1 1c0 1.25.2 2.45.57 3.57a1 1 0 0 1-.25 1z"/></svg>
          044-123 456 789
        </li>
        <li>
          <svg viewBox="0 0 24 24" fill="none" stroke="var(--blue)" stroke-width="2"><rect x="6" y="2" width="12" height="20" rx="2"/><line x1="11" y1="18" x2="13" y2="18"/></svg>
          044-123 456 789
        </li>
        <li>
          <svg viewBox="0 0 24 24" fill="var(--blue)"><path d="M2 5h20v14H2z"/><path d="M2 5l10 8 10-8" fill="none" stroke="var(--card)" stroke-width="1.6"/></svg>
          info@veldmark.com
        </li>
        <li>
          <svg viewBox="0 0 24 24" fill="none" stroke="var(--blue)" stroke-width="2"><circle cx="12" cy="12" r="10"/><ellipse cx="12" cy="12" rx="4" ry="10"/><line x1="2" y1="12" x2="22" y2="12"/></svg>
          www.veldmark.com
        </li>
      </ul>
    </div>
    <div class="stripe"><span class="stripe__red"></span><span class="stripe__blue"></span></div>
  </section>
</main>
</body>
</html>
```